Business Card - connecting 2 souls and beggining the journey of self discovery

Logo on the front
with tag line

On the back list of services and contact details

Seminars
workshops
Coaching
podcasts

Darren Whitlow
Health & Wellbeing Life Coach
0491 372 615
darren@brightcoreliving.example
brightcoreliving.example

Industry/Entity Type

Life Coaching

Contact Information for Business Card

I like the use of colour from the logo to be used. I'm not a fan of white.

Requirements
Must have
• My tagline: The journey home starts with you
Nice to have
• Use of colour that is in the mind body soul logo

```html
<!DOCTYPE html>
<html lang="en">
<head>
<meta charset="utf-8">
<title>Bright Core Living – Business Card</title>
<link href="https://fonts.googleapis.com/css2?family=Open+Sans:wght@400;600;700&display=swap" rel="stylesheet">
<style>
  :root {
    --stage: #2a2a2c;
    --card-dark: #161617;
    --card-light: #f7f7f6;
    --ink-grey: #8a8a8c;
    --ink-dark: #5b5b5d;
    --ink-soft: #d9d9d9;
    --green: #4cb87a;
    --pink: #ea4a6c;
    --orange: #f6a13a;
    --teal-line: #9fd3bd;
    --mark-start: #f0508a;
    --mark-mid: #f7b733;
    --mark-end: #5fc46f;
  }
  * { margin: 0; padding: 0; box-sizing: border-box; }
  html, body { width: 1200px; height: 900px; overflow: hidden; }
  body {
    background: var(--stage);
    font-family: "Open Sans", Arial, sans-serif;
    display: flex;
    flex-direction: column;
    align-items: center;
    justify-content: center;
    gap: 36px;
  }
  .card {
    width: 720px;
    height: 400px;
    position: relative;
    overflow: hidden;
    border-radius: 4px;
    box-shadow: 0 10px 30px rgba(0,0,0,.35);
  }
  .mark {
    border-radius: 50%;
    background: linear-gradient(135deg, var(--mark-start), var(--mark-mid) 50%, var(--mark-end));
  }

  /* Services side */
  .card--services {
    background: var(--card-dark);
    display: flex;
    flex-direction: column;
    align-items: center;
    justify-content: center;
  }
  .card--services .mark { width: 110px; height: 110px; margin-bottom: 26px; }
  .card--services .brand-name {
    font-size: 34px; font-weight: 600; color: var(--ink-grey); letter-spacing: -0.5px;
  }
  .services {
    list-style: none; display: flex; gap: 10px; margin-top: 18px;
    color: var(--ink-soft); font-size: 16px;
  }
  .services li { display: flex; align-items: center; gap: 10px; }
  .services li + li::before {
    content: ""; width: 6px; height: 6px; border-radius: 50%; background: var(--green);
  }

  /* Contact side */
  .card--contact { background: var(--card-light); }
  .brand-block {
    position: absolute; right: 48px; top: 46px; text-align: left;
  }
  .brand-block .mark { width: 72px; height: 72px; margin: 0 0 12px auto; }
  .brand-block .brand-name {
    font-size: 28px; font-weight: 600; color: var(--ink-grey); letter-spacing: -0.5px;
  }
  .tagline { font-size: 15px; font-weight: 600; color: var(--ink-grey); }
  .divider {
    position: absolute; left: 48px; right: 48px; top: 214px;
    height: 1px; background: var(--teal-line);
  }
  .website {
    position: absolute; right: 48px; top: 232px;
    font-size: 15px; color: var(--ink-dark);
  }
  .person { position: absolute; left: 48px; bottom: 54px; }
  .person-name {
    font-size: 24px; font-weight: 700; color: var(--green); text-transform: uppercase;
  }
  .person-role {
    font-size: 15px; font-weight: 700; color: var(--pink); text-transform: uppercase;
    margin-bottom: 10px;
  }
  .contact-line {
    display: flex; align-items: center; gap: 8px; font-size: 15px; color: var(--ink-dark);
    line-height: 1.5;
  }
  .contact-line svg { width: 14px; height: 14px; fill: var(--green); }
  .edge-bands { position: absolute; left: 0; right: 0; bottom: 0; }
  .edge-bands span { display: block; height: 4px; }
  .band-pink { background: var(--pink); }
  .band-orange { background: var(--orange); }
  .band-green { background: var(--green); height: 8px !important; }
</style>
</head>
<body>
  <section class="card card--services">
    <div class="mark" aria-hidden="true"></div>
    <h1 class="brand-name">Bright Core Living</h1>
    <ul class="services">
      <li>Seminars</li>
      <li>Workshops</li>
      <li>Coaching</li>
      <li>Podcasts</li>
    </ul>
  </section>

  <section class="card card--contact">
    <div class="brand-block">
      <div class="mark" aria-hidden="true"></div>
      <h2 class="brand-name">Bright Core Living</h2>
      <p class="tagline">The journey home starts with you</p>
    </div>
    <div class="divider"></div>
    <p class="website">www.brightcoreliving.example</p>
    <div class="person">
      <p class="person-name">Darren Whitlow</p>
      <p class="person-role">Health &amp; Wellbeing Life Coach</p>
      <p class="contact-line">
        <svg viewBox="0 0 24 24" aria-hidden="true"><path d="M6.6 10.8a15.1 15.1 0 0 0 6.6 6.6l2.2-2.2a1 1 0 0 1 1-.25 11.4 11.4 0 0 0 3.6.57 1 1 0 0 1 1 1V20a1 1 0 0 1-1 1A17 17 0 0 1 3 4a1 1 0 0 1 1-1h3.5a1 1 0 0 1 1 1c0 1.25.2 2.45.57 3.6a1 1 0 0 1-.25 1z"/></svg>
        0491 372 615
      </p>
      <p class="contact-line">
        <svg viewBox="0 0 24 24" aria-hidden="true"><path d="M2 5h20v14H2z M2 5l10 8 10-8" fill="var(--green)"/><path d="M3 6l9 7 9-7" fill="none" stroke="#fff" stroke-width="1.6"/></svg>
        darren@brightcoreliving.example
      </p>
    </div>
    <div class="edge-bands" aria-hidden="true">
      <span class="band-pink"></span>
      <span class="band-orange"></span>
      <span class="band-green"></span>
    </div>
  </section>
</body>
</html>
```